Lar Ventura Banners Ads

We need to create 4 animated banners ads in GIF (3 arts for each banner) to Lar Ventura Publiclik Display Campaign
Lar Ventura is an ecommerce in Brazil that sells high end home products.
It is a Branding Campaign, but we will add products images on it, so it has to be very sofisticated like the brand is.

We need 4 designs - 1 design for each size:

- Retângulo inline (300 X 250)
- Retângulo grande (336 x 280)
- Banner (468 x 60)
- Cabeçalho (728 x 90)

Please, find the briefing in pdf archive attached

Text we can work on th banners:

1 - Sofisticação com exclusividade para sua Casa!
2 - chique, exclusivo e encantador
3 - Encantador, sofisticado e exclusivo

The final image has to have Fontenelle´s Logo, Lar Ventura´s logo and a call to action:

Confira nossos produtos exclusivos!

_________________________________________________________________
UPDATE

Please, for the colors, take the ones from pdf; (use more collors chics, silver and white, but not only this colors);
Don't forget the CALL TO ACTION " Confira nossos Produtos Exclusivos!"

If you'd like to meet the brand and the target, here is the page on Facebook: https://www.rededeamigos.example/LarVenturaHomeVentura

But please, DO NOT COPY ANY OF THESE EXAMPLES ON THE PAGE.
We need something more executive.

Target Market(s)

Woman 30+
Trendy, modern, sofisticated, married or mum, cosmopolitan,
UPPERCLASS

Industry/Entity Type

Call

Font styles to use
Script
Other font styles liked:
• ColfaxTrial

Requirements
Must have
• Product images
Text
Product Image + Call to action on final layer with logos
As you will see the example in pdf archive attached
Nice to have
• frames
Should not have
• people
flowers
girlish drawing

```html
<!DOCTYPE html>
<html lang="pt-BR">
<head>
<meta charset="utf-8">
<title>Lar Ventura — Banners</title>
<link rel="stylesheet" href="https://fonts.googleapis.com/css2?family=Archivo:wght@500;600;700&display=swap">
<style>
  :root {
    --stage: #eeeae5;
    --white: #ffffff;
    --panel-grey: #d3d3d3;
    --ink: #141414;
    --logo-grey: #8c8680;
    --cta-pink: #e2449c;
    --cta-text: #ffffff;
    --photo-light: #eef3f6;
    --photo-mid: #c9d6df;
    --photo-navy: #234a7c;
    --photo-deep: #183760;
  }
  * { box-sizing: border-box; margin: 0; padding: 0; }
  html, body { width: 1200px; height: 900px; overflow: hidden; }
  body {
    background: var(--stage);
    font-family: "Archivo", Arial, sans-serif;
    position: relative;
  }
  .banner {
    position: absolute;
    background: var(--white);
    overflow: hidden;
    box-shadow: 0 2px 8px rgba(0,0,0,.12);
  }
  .brand-name {
    font-family: "Archivo", Arial, sans-serif;
    font-weight: 600;
    color: var(--logo-grey);
    letter-spacing: .02em;
    white-space: nowrap;
    position: absolute;
    line-height: 1;
  }
  .cta {
    position: absolute;
    background: var(--cta-pink);
    color: var(--cta-text);
    font-weight: 700;
    text-align: center;
    display: flex;
    align-items: center;
    justify-content: center;
    line-height: 1.05;
    white-space: nowrap;
  }
  .headline {
    position: absolute;
    font-weight: 600;
    color: var(--ink);
    text-align: center;
    line-height: 1.3;
    white-space: nowrap;
  }
  .product-photo {
    position: absolute;
    background:
      linear-gradient(170deg, var(--photo-light) 0%, var(--photo-light) 38%, transparent 39%),
      linear-gradient(180deg, var(--photo-mid) 0%, #f4f6f8 45%, var(--photo-navy) 70%, var(--photo-deep) 100%);
  }
  .grey-panel {
    position: absolute;
    top: 0; bottom: 0;
    background: var(--panel-grey);
  }
  .pointer { position: absolute; }

  /* Cabeçalho 728x90 */
  .leaderboard { left: 177px; top: 171px; width: 853px; height: 105px; }
  .leaderboard .brand-name { left: 8px; top: 10px; font-size: 27px; }
  .leaderboard .cta { left: 14px; top: 52px; width: 151px; height: 42px; border-radius: 8px; font-size: 13.5px; }
  .leaderboard .grey-panel { left: 209px; width: 262px; }
  .leaderboard .pointer { left: 209px; top: 16px; }
  .leaderboard .headline { left: 209px; width: 262px; top: 15px; font-size: 18.5px; }
  .leaderboard .product-photo { left: 471px; top: 0; width: 382px; height: 105px; }

  /* Banner 468x60 */
  .banner-strip { left: 329px; top: 368px; width: 548px; height: 70px; }
  .banner-strip .brand-name { left: 5px; top: 7px; font-size: 18px; }
  .banner-strip .cta { left: 9px; top: 35px; width: 98px; height: 29px; border-radius: 6px; font-size: 9px; }
  .banner-strip .grey-panel { left: 135px; width: 167px; }
  .banner-strip .pointer { left: 135px; top: 10px; }
  .banner-strip .headline { left: 135px; width: 167px; top: 9px; font-size: 11.5px; }
  .banner-strip .product-photo { left: 302px; top: 0; width: 246px; height: 70px; }

  /* Retângulo inline 300x250 */
  .rect-inline { left: 309px; top: 533px; width: 352px; height: 293px; }
  .rect-inline .product-photo { left: 0; top: 0; width: 352px; height: 240px; }
  .rect-inline .headline { left: 10px; width: 190px; top: 21px; font-size: 18.5px; }
  .rect-inline .pointer { left: 302px; top: 228px; }
  .rect-inline .cta { left: 3px; top: 244px; width: 154px; height: 45px; border-radius: 8px; font-size: 14px; }
  .rect-inline .brand-name { left: 165px; top: 253px; font-size: 27px; }

  /* Retângulo grande 336x280 */
  .rect-large { left: 705px; top: 516px; width: 394px; height: 328px; }
  .rect-large .product-photo { left: 0; top: 0; width: 394px; height: 266px; }
  .rect-large .headline { left: 12px; width: 192px; top: 21px; font-size: 20px; }
  .rect-large .pointer { left: 344px; top: 253px; }
  .rect-large .cta { left: 3px; top: 273px; width: 172px; height: 50px; border-radius: 8px; font-size: 15px; }
  .rect-large .brand-name { left: 184px; top: 283px; font-size: 29px; }
</style>
</head>
<body>

  <section class="banner leaderboard" aria-label="Cabeçalho 728x90">
    <span class="brand-name">Lar Ventura</span>
    <a class="cta">Confira nossos<br>Produtos Exclusivos!</a>
    <div class="grey-panel"></div>
    <svg class="pointer" width="13" height="24" viewBox="0 0 13 24"><polygon points="0,0 13,12 0,24" fill="#ffffff"/></svg>
    <p class="headline">Sofisticação com<br>exclusividade<br>para sua Casa!</p>
    <div class="product-photo" role="img" aria-label="Foto de produto: cama com travesseiros brancos e colcha azul-marinho"></div>
  </section>

  <section class="banner banner-strip" aria-label="Banner 468x60">
    <span class="brand-name">Lar Ventura</span>
    <a class="cta">Confira nossos<br>Produtos Exclusivos!</a>
    <div class="grey-panel"></div>
    <svg class="pointer" width="9" height="16" viewBox="0 0 9 16"><polygon points="0,0 9,8 0,16" fill="#ffffff"/></svg>
    <p class="headline">Sofisticação com<br>exclusividade<br>para sua Casa!</p>
    <div class="product-photo" role="img" aria-label="Foto de produto: cama com travesseiros brancos e colcha azul-marinho"></div>
  </section>

  <section class="banner rect-inline" aria-label="Retângulo inline 300x250">
    <div class="product-photo" role="img" aria-label="Foto de produto: cama com cabeceira de ferro, travesseiros brancos e colcha azul-marinho"></div>
    <p class="headline">Sofisticação com<br>exclusividade<br>para sua Casa!</p>
    <svg class="pointer" width="24" height="13" viewBox="0 0 24 13"><polygon points="0,13 12,0 24,13" fill="#ffffff"/></svg>
    <a class="cta">Confira nossos<br>Produtos Exclusivos!</a>
    <span class="brand-name">Lar Ventura</span>
  </section>

  <section class="banner rect-large" aria-label="Retângulo grande 336x280">
    <div class="product-photo" role="img" aria-label="Foto de produto: cama com cabeceira de ferro, travesseiros brancos e colcha azul-marinho"></div>
    <p class="headline">Sofisticação com<br>exclusividade<br>para sua Casa!</p>
    <svg class="pointer" width="26" height="14" viewBox="0 0 26 14"><polygon points="0,14 13,0 26,14" fill="#ffffff"/></svg>
    <a class="cta">Confira nossos<br>Produtos Exclusivos!</a>
    <span class="brand-name">Lar Ventura</span>
  </section>

</body>
</html>
```